Sandwich Board and Poster design promoting a medical aesthetic clinic

I am looking for a clean, modern and relaxing design promoting a medical physician-led aesthetic clinic.
Services offered are neuromodulator treatment (Dyneline) and Dermal Fillers.
Logo must be included.
Use the tag line "Refresh your look, revive your spirit."
Address is 204-205 27361 93 Ave, Surrey, K7P 2R4
604-555-0172
email - info@brightmoorskin.ca
www.brightmoorskin.ca

```html
<!DOCTYPE html>
<html lang="en">
<head>
<meta charset="utf-8">
<title>Brightmoor Skin – Poster</title>
<link href="https://fonts.googleapis.com/css2?family=Anton&family=Open+Sans:wght@300;400;600;700&display=swap" rel="stylesheet">
<style>
  :root {
    --navy: #1f3d63;
    --navy-deep: #1a3558;
    --gold: #e2b92b;
    --gold-dark: #b9932c;
    --white: #ffffff;
    --backdrop: #e9e9e9;
    --skin-light: #d9b49a;
    --skin-mid: #b98a6c;
    --hair: #8a6a4f;
  }
  * { box-sizing: border-box; margin: 0; padding: 0; }
  html, body { width: 1200px; height: 856px; overflow: hidden; }
  body { background: var(--backdrop); position: relative; font-family: "Open Sans", sans-serif; }

  .poster {
    position: absolute; left: 317px; top: 28px;
    width: 566px; height: 800px;
    background: var(--navy);
    overflow: hidden;
    box-shadow: 0 6px 24px rgba(0,0,0,0.18);
  }

  .photo-profiles {
    position: absolute; left: 0; top: 0; width: 380px; height: 300px;
    background: linear-gradient(100deg, var(--hair) 0%, var(--skin-mid) 25%, var(--skin-light) 55%, var(--skin-mid) 80%, rgba(31,61,99,0) 100%);
    -webkit-mask-image: linear-gradient(to bottom, #000 80%, transparent 100%);
            mask-image: linear-gradient(to bottom, #000 80%, transparent 100%);
  }

  .brand {
    position: absolute; left: 381px; top: 110px; width: 160px;
    text-align: center; color: var(--white);
    font-family: "Open Sans", sans-serif; font-weight: 400;
    font-size: 19px; letter-spacing: 5px; line-height: 1.25;
  }

  .headline {
    position: absolute; left: 0; top: 306px; width: 566px;
    text-align: center; color: var(--white);
    font-family: "Anton", sans-serif; font-weight: 400;
    font-size: 66px; line-height: 72px; letter-spacing: -0.5px;
  }
  .headline .accent { color: var(--gold); }

  .services-intro {
    position: absolute; left: 0; top: 460px; width: 566px;
    text-align: center; color: var(--white);
    font-weight: 300; font-size: 17px;
  }
  .services-list {
    position: absolute; left: 0; top: 484px; width: 566px;
    text-align: center; color: var(--white);
    font-weight: 600; font-size: 14px; white-space: nowrap;
  }
  .services-list .primary { color: var(--gold); font-size: 22px; }

  .photo-treatment {
    position: absolute; left: 185px; top: 541px; width: 381px; height: 223px;
    background: radial-gradient(ellipse at 60% 55%, var(--skin-light) 0%, var(--skin-mid) 45%, var(--hair) 70%, rgba(31,61,99,0) 100%);
  }

  .contact {
    position: absolute; left: 24px; top: 598px; color: var(--white);
  }
  .contact .address { font-size: 14.5px; line-height: 21px; }
  .contact .phone { color: var(--gold); font-weight: 700; font-size: 24px; margin-top: 8px; line-height: 30px; }
  .contact .email { font-size: 14.5px; line-height: 22px; }

  .web-band {
    position: absolute; left: 0; bottom: 0; width: 566px; height: 36px;
    background: linear-gradient(90deg, var(--gold) 0%, var(--gold) 60%, var(--gold-dark) 100%);
    display: flex; align-items: center; justify-content: center;
    color: var(--navy-deep); font-weight: 700; font-size: 15px; letter-spacing: 4px;
  }
</style>
</head>
<body>
  <main class="poster">
    <div class="photo-profiles" role="img" aria-label="Photo of four women in side profile, lined up in a row"></div>

    <div class="brand">BRIGHTMOOR<br>SKIN</div>

    <h1 class="headline">
      Refresh your <span class="accent">look,</span><br>
      revive your <span class="accent">spirit</span>
    </h1>

    <p class="services-intro">Services offered are</p>
    <p class="services-list"><span class="primary">Neuromodulator Treatment</span> (Dyneline) and Dermal Fillers</p>

    <div class="photo-treatment" role="img" aria-label="Photo of a woman lying back receiving a forehead injection from gloved hands"></div>

    <address class="contact" style="font-style:normal">
      <p class="address">204-205 27361 93 Ave,<br>Surrey, K7P 2R4</p>
      <p class="phone">604-555-0172</p>
      <p class="email">info@brightmoorskin.ca</p>
    </address>

    <footer class="web-band">www.brightmoorskin.ca</footer>
  </main>
</body>
</html>
```